Private lender of mortgages and rent to own housing

need a website that reflects real estate especially mortgage lending and rent to own houses..
Sections as follows
Home About Types of mortgages Rent to own Contact us
Target Market(s)
consumers who require non traditonal mortgages
Industry/Entity Type
Mortgage
Coding
Coded - Design and coding required
Number of Pages Required
4 page
Font styles to use
Sans Serif
Colors
Designer to choose colors to be used in the design.
Requirements
Must have
- background pictures on pages. with nice picture on homepage of houses or a community
Nice to have
- contact us form i supplied a ink to

```html
<!DOCTYPE html>
<html lang="en">
<head>
<meta charset="utf-8">
<title>Harborline Lending Group</title>
<link rel="stylesheet" href="https://fonts.googleapis.com/css2?family=Josefin+Sans:wght@300;400;600;700&family=Open+Sans:ital,wght@0,400;0,600;0,700;1,400&display=swap">
<style>
:root{
  --navy:#2e2a6b;
  --navy-deep:#2b2763;
  --ink:#222;
  --text:#777;
  --muted:#999;
  --line:#ddd;
  --band:#f5f5f5;
  --white:#fff;
  --star:#f5c518;
}
*{box-sizing:border-box;margin:0;padding:0}
html,body{width:1200px;height:2995px;overflow:hidden;background:var(--white)}
body{font-family:"Open Sans",sans-serif;color:var(--text);position:relative}
.abs{position:absolute}
.head{font-family:"Josefin Sans",sans-serif;color:var(--ink)}

/* header */
.site-header{position:absolute;left:0;top:0;width:1200px;height:94px;background:var(--white)}
.brand{position:absolute;left:100px;top:62px;font-family:"Josefin Sans",sans-serif;font-weight:700;font-size:17px;color:var(--navy);letter-spacing:.3px}
.contact-top{position:absolute;top:14px;right:96px;display:flex;gap:30px;font-size:14px;color:var(--ink);align-items:center}
.contact-top span{display:flex;align-items:center;gap:10px}
.ic-circle{width:30px;height:30px;border-radius:50%;border:1px solid #bbb;display:flex;align-items:center;justify-content:center}
.ic-circle.fill{background:var(--navy);border:none}
.main-nav{position:absolute;top:60px;right:96px;display:flex;gap:34px;font-family:"Josefin Sans",sans-serif;font-size:17px;color:var(--ink);align-items:center}
.main-nav .active{border-bottom:2px solid var(--navy);padding-bottom:3px;color:var(--navy)}

/* hero */
.hero{position:absolute;left:0;top:94px;width:1200px;height:496px;overflow:hidden}
.hero-photo{position:absolute;inset:0;background:linear-gradient(180deg,#4d5a4a 0%,#6d7a66 35%,#8e8a7c 55%,#5f7e3a 80%,#6c9a34 100%)}
.hero-title{position:absolute;top:130px;width:100%;text-align:center;font-family:"Josefin Sans",sans-serif;font-size:66px;color:var(--white);font-weight:400}
.hero-sub{position:absolute;top:206px;width:100%;text-align:center;font-size:22px;color:var(--white)}
.hero-btn{position:absolute;left:505px;top:262px;width:190px;height:50px;border:2px solid var(--white);border-radius:25px;color:var(--white);font-family:"Josefin Sans",sans-serif;font-weight:600;font-size:16px;display:flex;align-items:center;justify-content:center}
.dots{position:absolute;top:396px;left:562px;display:flex;gap:8px}
.dots i{width:12px;height:12px;border-radius:50%;border:2px solid var(--white)}
.dots i.on{background:var(--white)}
.hero-wave{position:absolute;left:0;bottom:0}

/* welcome */
.welcome-kicker{position:absolute;left:96px;top:648px;font-size:29px;font-weight:300}
.welcome-title{position:absolute;left:96px;top:690px;font-size:27px;font-weight:700;letter-spacing:.5px}
.welcome-copy{position:absolute;left:96px;top:740px;width:480px;font-size:14px;line-height:27px}
.welcome-copy p+p{margin-top:26px}
.btn-outline{position:absolute;height:44px;border:2px solid #8c8aa8;border-radius:22px;font-family:"Josefin Sans",sans-serif;font-weight:700;font-size:14px;color:var(--navy);display:flex;align-items:center;justify-content:center}
.video{position:absolute;left:620px;top:672px;width:482px;height:312px;box-shadow:0 0 0 6px #fff,0 2px 10px rgba(0,0,0,.2);background:linear-gradient(135deg,#c9a27a 0%,#e6e2dc 40%,#f4f4f4 60%,#8a7055 100%)}
.play{position:absolute;left:210px;top:126px;width:60px;height:60px;border-radius:50%;background:#2a2a2a;display:flex;align-items:center;justify-content:center}

/* mortgages */
.types{position:absolute;left:0;top:1094px;width:1200px;height:498px;background:var(--band)}
.section-title{position:absolute;width:100%;text-align:center;font-family:"Josefin Sans",sans-serif;font-size:29px;color:var(--ink);font-weight:300}
.section-title b{font-weight:700}
.type{position:absolute;top:142px;width:260px;text-align:center}
.type .ring{width:140px;height:140px;border-radius:50%;border:1px solid #9a9a9a;margin:0 auto;display:flex;align-items:center;justify-content:center}
.type h3{font-family:"Josefin Sans",sans-serif;font-weight:400;font-size:20px;color:var(--ink);margin-top:34px}
.type p{font-size:13.5px;line-height:26px;margin-top:10px}
.type .more{font-family:"Josefin Sans",sans-serif;font-weight:700;font-size:14px;color:#555;margin-top:14px}
.type.active .ring{border-color:var(--navy)}
.type.active h3,.type.active p,.type.active .more{color:var(--navy)}

/* blog */
.post{position:absolute;top:1758px;width:324px}
.post-photo{height:210px;position:relative}
.date{position:absolute;left:-6px;bottom:-6px;width:48px;height:60px;background:var(--navy);color:var(--white);text-align:center}
.date b{display:block;font-family:"Josefin Sans",sans-serif;font-size:22px;padding-top:10px}
.date small{font-size:12px}
.post h3{font-family:"Josefin Sans",sans-serif;font-size:20px;font-weight:600;color:var(--ink);margin-top:36px}
.post p{font-size:12.5px;line-height:20px;margin-top:12px;padding-bottom:14px;border-bottom:1px solid var(--line)}
.meta{font-size:11.5px;margin-top:12px;display:flex;gap:18px;align-items:center}
.meta span{display:flex;gap:6px;align-items:center}

/* testimonials */
.testimonials{position:absolute;left:0;top:2220px;width:1200px;height:378px;background:linear-gradient(90deg,#332e6e,#3b3577 50%,#332e6e)}
.testimonials .section-title{color:var(--white);top:80px}
.quote{position:absolute;top:132px;width:330px}
.avatar{position:absolute;left:0;top:0;width:72px;height:72px;border-radius:50%;border:3px solid var(--white);background:linear-gradient(180deg,#d9c8b8,#a08a78)}
.quote-body{position:absolute;left:90px;top:0;width:240px;color:var(--white)}
.quote-body p{font-style:italic;font-size:11.5px;line-height:22px}
.quote-body p::before{content:"\201C";font-size:24px;font-weight:700;margin-right:6px;vertical-align:-6px}
.who{font-size:10.5px;font-weight:700;margin-top:14px;text-transform:uppercase}
.role{font-size:9.5px;font-style:italic;margin-top:2px}
.stars{margin-top:18px;display:flex;gap:3px}
.arrow{position:absolute;top:2414px;width:34px;height:34px;border-radius:50%;border:1px solid rgba(255,255,255,.8);display:flex;align-items:center;justify-content:center}

/* footer */
.footer-brand{position:absolute;left:96px;top:2802px;font-family:"Josefin Sans",sans-serif;font-weight:700;font-size:16px;color:var(--navy)}
.fcol{position:absolute;top:2682px}
.fcol h4{font-family:"Josefin Sans",sans-serif;font-weight:400;font-size:18px;color:var(--ink)}
.fcol h4 b{font-weight:700}
.links{list-style:none;margin-top:22px;font-size:12.5px;line-height:28.5px;color:#555}
.fcol .note{font-size:12.5px;line-height:22px;margin-top:24px;color:#555}
.field{margin-top:18px;border-bottom:1px solid var(--line);width:256px;padding-bottom:8px;font-size:11px;color:#aaa;padding-left:14px}
.sub-btn{margin-top:14px;width:102px;height:34px;border:1px solid #888;border-radius:17px;display:flex;align-items:center;justify-content:center;font-family:"Josefin Sans",sans-serif;font-size:12px;font-weight:700;color:var(--ink)}
.citem{display:flex;gap:18px;font-size:12.5px;line-height:20px;color:#555;margin-top:20px}
.citem:first-of-type{margin-top:28px}
.footer-rule{position:absolute;left:96px;top:2922px;width:1008px;border-top:1px solid var(--line)}
.copyright{position:absolute;left:96px;top:2952px;font-size:12px;color:#555}
.social{position:absolute;right:96px;top:2944px;display:flex;gap:10px}
.social i{width:26px;height:26px;border-radius:50%;border:1px solid #999}
</style>
</head>
<body>

<header class="site-header">
  <div class="brand">HARBORLINE LENDING GROUP</div>
  <div class="contact-top">
    <span><i class="ic-circle"><svg width="14" height="14" viewBox="0 0 24 24"><path fill="#222" d="M6.6 10.8a15.1 15.1 0 0 0 6.6 6.6l2.2-2.2c.3-.3.7-.4 1-.2 1.1.4 2.3.6 3.6.6.6 0 1 .4 1 1V20c0 .6-.4 1-1 1A17 17 0 0 1 3 4c0-.6.4-1 1-1h3.5c.6 0 1 .4 1 1 0 1.3.2 2.5.6 3.6.1.3 0 .7-.2 1z"/></svg></i>1 800 555 0142</span>
    <span><i class="ic-circle fill"><svg width="14" height="12" viewBox="0 0 24 20"><path fill="#fff" d="M2 2h20v16H2zM3 3l9 7 9-7"/><path fill="none" stroke="#2e2a6b" stroke-width="2" d="M3 3l9 7 9-7"/></svg></i>hello@harborlinelending.ca</span>
  </div>
  <nav class="main-nav">
    <span class="active">Home</span><span>About</span><span>Types of mortgages</span><span>Rent to own</span><span>Contact us</span>
    <svg width="16" height="16" viewBox="0 0 24 24"><circle cx="10" cy="10" r="7" fill="none" stroke="#222" stroke-width="3"/><path d="M15 15l7 7" stroke="#222" stroke-width="3"/></svg>
  </nav>
</header>

<section class="hero">
  <div class="hero-photo" role="img" aria-label="Modern two-storey house with wood and white facade among tall trees and a green lawn"></div>
  <h1 class="hero-title">Harborline Lending Group</h1>
  <p class="hero-sub">We provide mortgage lending and rent to own houses</p>
  <div class="hero-btn">GET A QUOTE</div>
  <div class="dots"><i class="on"></i><i></i><i></i><i></i></div>
  <svg class="hero-wave" width="1200" height="120" viewBox="0 0 1200 120">
    <path d="M0 70 C300 10 700 100 1200 20 L1200 120 L0 120Z" fill="#fff"/>
    <path d="M0 78 C300 18 700 108 1200 28" fill="none" stroke="#2e2a6b" stroke-width="8"/>
    <path d="M0 92 C300 40 700 118 1200 40" fill="none" stroke="#9a9a9a" stroke-width="4"/>
  </svg>
</section>

<section>
  <div class="welcome-kicker head">WELCOME TO</div>
  <div class="welcome-title head">HARBORLINE LENDING GROUP</div>
  <div class="welcome-copy">
    <p>Harborline Lending Group is a private lender of 1 st ,2 nd , construction and bridge mortgages in Simcoe County area.</p>
    <p>HLG offers a wide array of financing options to provide assistance to those of you that do not meet the bank's criteria. The reasons could range from bruised credit to inability to provide the banks with the required documentation to meet income qualification guidelines.</p>
  </div>
  <div class="btn-outline" style="left:96px;top:958px;width:134px">READ MORE</div>
  <div class="video" role="img" aria-label="Video still of hands signing a mortgage document and handing over house keys">
    <div class="play"><svg width="20" height="22" viewBox="0 0 20 22"><path d="M3 1l16 10L3 21z" fill="#fff"/></svg></div>
  </div>
</section>

<section class="types">
  <h2 class="section-title" style="top:78px">TYPES OF <b>MORTGAGES</b></h2>
  <div class="type" style="left:80px">
    <div class="ring"><svg width="76" height="40" viewBox="0 0 76 40" fill="#666"><path d="M2 14 Q38 -2 74 14 L74 20 Q38 6 2 20Z"/><rect x="14" y="10" width="6" height="28"/><rect x="56" y="10" width="6" height="28"/><rect x="0" y="20" width="76" height="5"/></svg></div>
    <h3>Bridge Financing</h3>
    <p>We can help you close the sale of your purchase before the property</p>
    <div class="more">READ MORE</div>
  </div>
  <div class="type active" style="left:340px">
    <div class="ring"><svg width="66" height="56" viewBox="0 0 66 56" fill="#2e2a6b"><rect x="4" y="34" width="10" height="20"/><rect x="19" y="26" width="10" height="28"/><rect x="34" y="30" width="10" height="24"/><rect x="49" y="16" width="10" height="38"/><path d="M6 22 L24 12 L39 18 L58 4" stroke="#2e2a6b" stroke-width="3" fill="none"/><circle cx="6" cy="22" r="3"/><circle cx="24" cy="12" r="3"/><circle cx="39" cy="18" r="3"/><circle cx="58" cy="4" r="3"/></svg></div>
    <h3>Debt Consolidation</h3>
    <p>We can help you close the sale of your purchase before the property</p>
    <div class="more">READ MORE</div>
  </div>
  <div class="type" style="left:600px">
    <div class="ring"><svg width="70" height="52" viewBox="0 0 70 52"><rect x="2" y="18" width="48" height="28" fill="none" stroke="#555" stroke-width="3"/><rect x="8" y="12" width="48" height="28" fill="#fff" stroke="#555" stroke-width="3"/><circle cx="32" cy="26" r="8" fill="#555"/><text x="32" y="30" font-size="11" text-anchor="middle" fill="#fff" font-family="sans-serif">$</text><circle cx="58" cy="12" r="10" fill="#555"/><path d="M52 9h12M52 15h12" stroke="#fff" stroke-width="2"/></svg></div>
    <h3>Equity take out</h3>
    <p>We can help you close the sale of your purchase before the property</p>
    <div class="more">READ MORE</div>
  </div>
  <div class="type" style="left:860px">
    <div class="ring"><svg width="60" height="60" viewBox="0 0 60 60"><path d="M4 28 L30 6 L56 28" fill="none" stroke="#555" stroke-width="4"/><rect x="12" y="26" width="36" height="30" fill="none" stroke="#555" stroke-width="3"/><rect x="22" y="34" width="18" height="18" fill="#555"/><text x="31" y="48" font-size="14" text-anchor="middle" fill="#fff" font-family="sans-serif">$</text></svg></div>
    <h3>Construction Financing</h3>
    <p>We can help you close the sale of your purchase before the property</p>
    <div class="more">READ MORE</div>
  </div>
</section>

<section>
  <h2 class="section-title" style="top:1680px">LATEST <b>BLOG</b></h2>
  <article class="post" style="left:96px">
    <div class="post-photo" role="img" aria-label="Large suburban family home with garage and landscaped front yard" style="background:linear-gradient(180deg,#9fc2e0,#8a8f8c 50%,#5d7a3c)"><div class="date"><b>01</b><small>NOV</small></div></div>
    <h3>Finibus Bonorum et Malorum</h3>
    <p>Nam libero tempore, cum soluta nobis est eligendi optio cumque nihil impedit quo minus id quod maxim.</p>
    <div class="meta"><span>● Sam Rowe</span><span>▪ 3 Comments</span></div>
  </article>
  <article class="post" style="left:440px">
    <div class="post-photo" role="img" aria-label="Loan agreement paper with a pen and calculator" style="background:linear-gradient(135deg,#e8e8e8,#bfbfbf 50%,#f2f2f2)"><div class="date"><b>01</b><small>NOV</small></div></div>
    <h3>Finibus Bonorum et Malorum</h3>
    <p>Nam libero tempore, cum soluta nobis est eligendi optio cumque nihil impedit quo minus id quod maxim.</p>
    <div class="meta"><span>● Sam Rowe</span><span>▪ 3 Comments</span></div>
  </article>
  <article class="post" style="left:784px">
    <div class="post-photo" role="img" aria-label="Two-storey house lit at dusk" style="background:linear-gradient(180deg,#7c9ac4,#a49a8a 55%,#6f6a5c)"><div class="date"><b>01</b><small>NOV</small></div></div>
    <h3>Finibus Bonorum et Malorum</h3>
    <p>Nam libero tempore, cum soluta nobis est eligendi optio cumque nihil impedit quo minus id quod maxim.</p>
    <div class="meta"><span>● Sam Rowe</span><span>▪ 3 Comments</span></div>
  </article>
</section>

<section class="testimonials" role="img" aria-label="Client testimonials over a navy-tinted photo of people meeting">
  <h2 class="section-title">CLIENT <b>TESTIMONIALS</b></h2>
  <div class="quote" style="left:98px">
    <div class="avatar"></div>
    <div class="quote-body">
      <p>At vero eos et accusamus et iustodio dignissimos ducimus qui blanditiipraesnt ium voluptatum deleniti atq.</p>
      <div class="who">Marla Dunmore</div><div class="role">Financial Services Professional</div>
      <div class="stars"><svg width="110" height="18" viewBox="0 0 110 18" fill="var(--star)"><g id="s"><path d="M9 1l2.4 5.2 5.6.6-4.2 3.8 1.2 5.6L9 13.3 4 16.2l1.2-5.6L1 6.8l5.6-.6z"/></g><use href="#s" x="22"/><use href="#s" x="44"/><use href="#s" x="66"/><use href="#s" x="88" fill="none" stroke="var(--star)"/></svg></div>
    </div>
  </div>
  <div class="quote" style="left:446px">
    <div class="avatar"></div>
    <div class="quote-body">
      <p>At vero eos et accusamus et iustodio dignissimos ducimus qui blanditiipraesnt ium voluptatum deleniti atq.</p>
      <div class="who">Tessa R. Vallin</div><div class="role">National Urban Fellow at the Houston</div>
      <div class="stars"><svg width="110" height="18" viewBox="0 0 110 18" fill="var(--star)"><use href="#s"/><use href="#s" x="22"/><use href="#s" x="44"/><use href="#s" x="66"/><use href="#s" x="88" fill="none" stroke="var(--star)"/></svg></div>
    </div>
  </div>
  <div class="quote" style="left:794px">
    <div class="avatar"></div>
    <div class="quote-body">
      <p>At vero eos et accusamus et iustodio dignissimos ducimus qui blanditiipraesnt ium voluptatum deleniti atq.</p>
      <div class="who">June Halvorsen</div><div class="role">Creative Strategist | Entrepreneur &amp; Upcoming</div>
      <div class="stars"><svg width="110" height="18" viewBox="0 0 110 18" fill="var(--star)"><use href="#s"/><use href="#s" x="22"/><use href="#s" x="44"/><use href="#s" x="66"/><use href="#s" x="88" fill="none" stroke="var(--star)"/></svg></div>
    </div>
  </div>
</section>
<div class="arrow" style="left:30px"><svg width="10" height="14" viewBox="0 0 10 14"><path d="M8 1L2 7l6 6" stroke="#fff" stroke-width="2" fill="none"/></svg></div>
<div class="arrow" style="left:1136px"><svg width="10" height="14" viewBox="0 0 10 14"><path d="M2 1l6 6-6 6" stroke="#fff" stroke-width="2" fill="none"/></svg></div>

<footer>
  <div class="footer-brand">HARBORLINE LENDING GROUP</div>
  <div class="fcol" style="left:400px">
    <h4>Quick <b>Links</b></h4>
    <ul class="links"><li>Home</li><li>About us</li><li>Types of mortgages</li><li>Rent to own</li><li>Contact us</li></ul>
  </div>
  <div class="fcol" style="left:580px">
    <h4>Newsletter <b>Subscription</b></h4>
    <p class="note">Register your Email Address to get<br>Information about us</p>
    <div class="field">Email Address</div>
    <div class="sub-btn">SUBSCRIBE</div>
  </div>
  <div class="fcol" style="left:890px">
    <h4>Contact <b>Us</b></h4>
    <div class="citem"><svg width="12" height="16" viewBox="0 0 12 16"><path d="M6 0a6 6 0 0 1 6 6c0 4-6 10-6 10S0 10 0 6a6 6 0 0 1 6-6z" fill="#2e2a6b"/><circle cx="6" cy="6" r="2" fill="#fff"/></svg><span>Level 12, 48 Birch Avenue<br>Barrie, ON</span></div>
    <div class="citem"><svg width="14" height="14" viewBox="0 0 24 24"><path fill="#2e2a6b" d="M6.6 10.8a15.1 15.1 0 0 0 6.6 6.6l2.2-2.2c.3-.3.7-.4 1-.2 1.1.4 2.3.6 3.6.6.6 0 1 .4 1 1V20c0 .6-.4 1-1 1A17 17 0 0 1 3 4c0-.6.4-1 1-1h3.5c.6 0 1 .4 1 1 0 1.3.2 2.5.6 3.6.1.3 0 .7-.2 1z"/></svg><span>1 800 555 0142</span></div>
    <div class="citem"><svg width="14" height="12" viewBox="0 0 24 20"><rect x="1" y="1" width="22" height="18" fill="#2e2a6b"/><path d="M2 3l10 8 10-8" stroke="#fff" stroke-width="2" fill="none"/></svg><span>hello@harborlinelending.ca</span></div>
  </div>
  <div class="footer-rule"></div>
  <div class="copyright">Copyrights © 2017, Harborline Lending Group. All rights reserved.</div>
  <div class="social"><i></i><i></i><i></i><i></i></div>
</footer>

</body>
</html>
```